Counseling Practice Business Card

I need a professional looking business card incorporating my new logo that was just completed. Card needs to incorporate my name and title, description of my specialty, my address, my phone number, my fax number, my email and my website URL. I need to be able to choose design on/with different paper colors and textures.
I do not have a lot of business card ideas so I am open to anything but I want bold,sharp, clear card without additional designs other than my logo (see attached file info). I am open to different color backgrounds or paper colors including black. I do not like traditional brackets around area codes in phone number or dashes between numbers in phone number. Am open to other ways of presenting including periods between numbers as appropriate. I do not know enough to know what I like yet but I want card to coordinate and work together with my logo. My practice emphasizes natural mental health interventions so any use of color (with background paper color or the blue and green in my logo) that elicits nature is nice. In addition to black, any natural brown or wood looking background might be desirable also. Most of the offerings so far look very similar and boring.

Target Market(s)

Potential therapy clients and other professionals

Contact Information for Business Card

Card information:
Gerald M. Whitcombe, Ph.D.
Licensed Clinical Psychologist
Integrative Health Coach
4812 Marlowe Ridge Blvd SE
Suite 310
Duluth, GA 30096
(770) 415-2983 phone
(770) 581-4096 fax
drgeraldwhitcombe@quillmarsh.net
brightfernwellness.net

Font styles to use
Serif
Sans Serif
Other font styles liked:
• anything that you think looks crisp, clear and easily readable

Requirements
Must have
• Any color used should coordinate with my logo design (see attached files).
• Card should be printed horizontally so top and bottom are longest sides of rectangle.
• Background color or paper color should complement and highlight logo. Do not like a white background. black, grey, brown or any color my logo would blend well with.
Nice to have
• I would like designer to utilize color to highlight letters/name or phone-fax-web symbols.
• Bottom edge of card could be highlighted if appropriate to an idea.
Should not have
• I would NOT want the card to have a pure white background at all.
• No clear cards.
• Cards should be oriented with long sides on bottom and top, NOT sides. DO NOT LIKE THIS THIN TALL ORIENTATION.

```html
<!DOCTYPE html>
<html lang="en">
<head>
<meta charset="utf-8">
<title>Brightfern Wellness – Business Card</title>
<link rel="stylesheet" href="https://fonts.googleapis.com/css2?family=Nunito:wght@800&family=Open+Sans:wght@400;600&family=Arimo:wght@400&display=swap">
<style>
  :root {
    --page-bg: #3a2418;
    --card-green: #4cbc45;
    --card-lime: #c9e34f;
    --card-glow: #f0ef62;
    --brand-green: #1b6a2c;
    --ink-white: #ffffff;
    --icon-ink: #2a2a2a;
  }
  html, body {
    margin: 0;
    padding: 0;
    width: 1200px;
    height: 1200px;
    overflow: hidden;
    background: var(--page-bg);
  }
  .canvas {
    position: relative;
    width: 1200px;
    height: 1200px;
  }
  .card {
    position: absolute;
    left: 75px;
    top: 300px;
    width: 1050px;
    height: 600px;
    background:
      radial-gradient(ellipse 380px 260px at 25% 28%, var(--card-glow) 0%, var(--card-lime) 40%, rgba(201,227,79,0) 100%),
      radial-gradient(ellipse 800px 600px at 55% 60%, #45b83f 0%, var(--card-green) 60%, #5cc24a 100%);
    box-shadow: 0 10px 30px rgba(0,0,0,0.45);
  }
  .identity-panel {
    position: absolute;
    left: 30px;
    top: 0;
    width: 480px;
    height: 600px;
    text-align: center;
  }
  .brand {
    position: absolute;
    left: 0;
    right: 0;
    top: 95px;
    margin: 0;
    font-family: "Open Sans", sans-serif;
    font-weight: 600;
    font-size: 56px;
    line-height: 1.05;
    color: var(--brand-green);
  }
  .identity {
    position: absolute;
    left: 0;
    right: 0;
    top: 355px;
    color: var(--ink-white);
  }
  .identity .name {
    font-family: "Nunito", sans-serif;
    font-weight: 800;
    font-size: 30px;
    margin: 0 0 6px;
  }
  .identity .title {
    font-family: "Open Sans", sans-serif;
    font-size: 25px;
    letter-spacing: 0.5px;
    line-height: 33px;
    margin: 0;
  }
  .contact {
    position: absolute;
    left: 560px;
    right: 30px;
    top: 95px;
    height: 420px;
    margin: 0;
    padding: 0;
    list-style: none;
    color: var(--ink-white);
  }
  .contact li {
    position: absolute;
    left: 0;
    right: 0;
    display: flex;
    align-items: center;
  }
  .contact .icon {
    width: 52px;
    height: 52px;
    flex: none;
    margin-right: 18px;
  }
  .contact .address { top: 0; align-items: flex-start; }
  .contact .address address {
    font-style: normal;
    font-family: "Arimo", sans-serif;
    font-size: 22px;
    line-height: 29px;
    margin-top: -2px;
  }
  .contact .line {
    font-family: "Open Sans", sans-serif;
    font-size: 24px;
    letter-spacing: 0.4px;
    white-space: nowrap;
  }
  .contact .email .line { font-size: 21px; letter-spacing: 0; }
  .contact .phone { top: 125px; }
  .contact .fax { top: 200px; }
  .contact .email { top: 275px; }
  .contact .web { top: 350px; }
</style>
</head>
<body>
<main class="canvas">
  <section class="card">
    <div class="identity-panel">
      <h1 class="brand">Brightfern<br>Wellness</h1>
      <div class="identity">
        <p class="name">Gerald M. Whitcombe, Ph.D.</p>
        <p class="title">Licensed Clinical Psychologist</p>
        <p class="title">Integrative Health Coach</p>
      </div>
    </div>

    <ul class="contact">
      <li class="address">
        <svg class="icon" viewBox="0 0 52 52" aria-hidden="true">
          <polygon points="14,4 38,4 50,26 38,48 14,48 2,26" fill="#fff"/>
          <path d="M12 27 L26 15 L40 27 M16 24 V37 H36 V24" fill="none" stroke="var(--icon-ink)" stroke-width="3" stroke-linejoin="round"/>
          <rect x="22" y="29" width="8" height="8" fill="none" stroke="var(--icon-ink)" stroke-width="2.5"/>
        </svg>
        <address>4812 Marlowe Ridge Blvd SE<br>Suite 310<br>Duluth, GA 30096</address>
      </li>
      <li class="phone">
        <svg class="icon" viewBox="0 0 52 52" aria-hidden="true">
          <polygon points="14,4 38,4 50,26 38,48 14,48 2,26" fill="#fff"/>
          <path d="M18 14 C15 16 14 19 16 24 C19 31 23 35 29 38 C33 40 36 38 38 35 L33 30 L29 33 C25 31 22 28 20 23 L23 20 Z" fill="var(--icon-ink)"/>
        </svg>
        <span class="line">770.415.2983</span>
      </li>
      <li class="fax">
        <svg class="icon" viewBox="0 0 52 52" aria-hidden="true">
          <polygon points="14,4 38,4 50,26 38,48 14,48 2,26" fill="#fff"/>
          <rect x="18" y="13" width="16" height="9" fill="none" stroke="var(--icon-ink)" stroke-width="2.5"/>
          <rect x="13" y="21" width="26" height="12" rx="2" fill="none" stroke="var(--icon-ink)" stroke-width="2.5"/>
          <rect x="18" y="29" width="16" height="10" fill="#fff" stroke="var(--icon-ink)" stroke-width="2.5"/>
          <path d="M21 33 H31 M21 36 H31" stroke="var(--icon-ink)" stroke-width="1.5"/>
        </svg>
        <span class="line">770.581.4096</span>
      </li>
      <li class="email">
        <svg class="icon" viewBox="0 0 52 52" aria-hidden="true">
          <polygon points="14,4 38,4 50,26 38,48 14,48 2,26" fill="#fff"/>
          <rect x="12" y="17" width="28" height="18" fill="none" stroke="var(--icon-ink)" stroke-width="2.5"/>
          <path d="M12 17 L26 28 L40 17" fill="none" stroke="var(--icon-ink)" stroke-width="2.5"/>
        </svg>
        <span class="line">drgeraldwhitcombe@quillmarsh.net</span>
      </li>
      <li class="web">
        <svg class="icon" viewBox="0 0 52 52" aria-hidden="true">
          <polygon points="14,4 38,4 50,26 38,48 14,48 2,26" fill="#fff"/>
          <circle cx="26" cy="26" r="13" fill="none" stroke="var(--icon-ink)" stroke-width="2.5"/>
          <ellipse cx="26" cy="26" rx="6" ry="13" fill="none" stroke="var(--icon-ink)" stroke-width="2"/>
          <path d="M13 26 H39 M15 19 H37 M15 33 H37" stroke="var(--icon-ink)" stroke-width="2"/>
        </svg>
        <span class="line">brightfernwellness.net</span>
      </li>
    </ul>
  </section>
</main>
</body>
</html>
```